Luxury Real Estate Website, Midwest, United States

We need web design services for a luxury website. We need IDX Integration with our MLS. We want this to be a very simple website with amazing graphics. We want it to link up with our PostPlume account in order to generate leads through a "More Information" Pop up on the main page. We want the main page to be covered with one large graphic that is a rolling slideshow of active listings of $400,000 and up from the IDX Integration. We need this website to give a very exclusive and sleek look. Lots of black is good... I will upload our logos in Black and Silver. We will also need an "About" page that we are going to call "Qeno Info". We want our graphics to be extremely impressive. Keep in mind, we are a company in the Midwest of the United States, and our real estate has a different look than homes in California or Florida. We need graphics that are realistic for the Midwest, yet still high-end.
Target Market(s)
Luxury Homeowners in the Midwest United States. The graphics needs to be pristine.
Industry/Entity Type
Real Estate
Coding
Coded - Design and coding required
Number of Pages Required
3 page
Requirements
Must have
- Large graphics with IDX Integration. The photos of real estate need to represent real estate that is common in the Midwest, United States. We also need PostPlume integration. We need a pop up that is titled "My Free Market Analysis" that makes them fill out a contact form asking for Full Name, Email Address, Phone Number and Address. This needs to be a pop up on the front page and will integrate with our PostPlume account. We also need a page called "About Qe No Home". And another page where clients can download informational PDFs. The main component needs to be a front page search engine connected with the IDX to access active listings from our MLS. I attached our logos and a sample front page of a website. I would love for ours to look similar.
Nice to have
- Lake House photos on midwest lakes are a plus.
Should not have
- Should not have clutter. This website needs to be clean, luxurious and exclusive.

```html
<!DOCTYPE html>
<html lang="en">
<head>
<meta charset="utf-8">
<title>Qeno Realty Group</title>
<link href="https://fonts.googleapis.com/css2?family=Jost:wght@300;400;500;600&family=Open+Sans:wght@400;600;700&display=swap" rel="stylesheet">
<style>
:root{
  --page:#f4f4f4;
  --white:#ffffff;
  --ink:#2b2b2b;
  --text:#555555;
  --muted:#8a8a8a;
  --rule:#9a9a9a;
  --black:#161616;
  --caption:#efefef;
  --band:#e6e6e6;
  --footer:#c8c8c8;
  --bottom:#6e6e6e;
  --btn:#a9b3bd;
  --field:#ededed;
  --dim:rgba(0,0,0,.66);
}
*{box-sizing:border-box;margin:0;padding:0}
html,body{width:1200px;height:2532px;overflow:hidden}
body{position:relative;background:var(--page);font-family:"Open Sans",sans-serif;color:var(--text)}
h2,h3{font-weight:400}
.abs{position:absolute}
.site-header{left:0;top:0;width:1200px;height:80px;background:var(--white)}
.brand{left:118px;top:22px;display:flex;align-items:center;gap:10px;font-family:"Jost",sans-serif;font-size:26px;font-weight:400;letter-spacing:1px;color:var(--ink)}
.brand .mark{width:10px;height:10px;background:var(--ink)}
.nav{left:580px;top:30px;display:flex;font-family:"Open Sans",sans-serif;font-size:13.5px;color:var(--ink)}
.nav a{display:block;height:32px;line-height:32px;padding:0 15px;color:inherit;text-decoration:none}
.nav a.active{background:var(--black);color:var(--white);border-radius:3px;padding:0 16px}
.photo-fill{background-size:100% 100%}
.hero{left:0;top:80px;width:1200px;height:528px;
  background:
    radial-gradient(ellipse 40% 18% at 22% 55%,rgba(120,110,100,.7),transparent 70%),
    radial-gradient(ellipse 55% 30% at 60% 30%,rgba(40,70,35,.8),transparent 75%),
    linear-gradient(180deg,#8fa3b4 0%,#5f7d55 18%,#2f4a2a 42%,#4a5d52 56%,#6e8aa0 70%,#3d5670 100%)}
.hero-arrow{top:340px}
.intro-img{left:113px;top:636px;width:221px;height:115px;
  background:radial-gradient(ellipse 50% 60% at 78% 45%,#6f8a5a,transparent 70%),linear-gradient(120deg,#5a2e1c,#a0653a 45%,#7a4a2a 60%,#3f5a40)}
.sec-title{font-family:"Jost",sans-serif;font-size:23px;font-weight:400;color:var(--ink);display:flex;align-items:center;gap:14px;letter-spacing:.3px}
.sec-title::after{content:"";flex:1;height:1px;background:var(--rule)}
.intro-title{left:361px;top:640px;width:724px}
.intro-text{left:361px;top:672px;width:724px;font-size:13px;line-height:22px}
.btn-more{display:block;background:var(--btn);color:var(--ink);font-size:11.5px;font-weight:600;text-align:center}
.intro-more{left:361px;top:727px;width:81px;height:23px;line-height:23px}
.popular-title{left:113px;top:791px;width:972px}
.card{width:235px;height:262px;background:var(--caption)}
.card .photo{height:194px}
.card h3{position:absolute;left:20px;top:208px;font-family:"Jost",sans-serif;font-size:20px;color:var(--ink)}
.card p{position:absolute;left:20px;top:234px;font-size:13px;color:var(--muted)}
.card svg{position:absolute;right:22px;top:218px}
.about-title{left:113px;top:1474px;width:482px}
.about-text{left:113px;top:1513px;width:482px;font-size:13px;line-height:21px;text-align:justify}
.about-more{left:113px;top:1617px;width:106px;height:29px;line-height:29px}
.about-img{left:608px;top:1455px;width:477px;height:203px;
  background:radial-gradient(ellipse 22% 30% at 25% 55%,rgba(150,90,70,.85),transparent 75%),radial-gradient(ellipse 18% 22% at 75% 62%,rgba(120,80,60,.7),transparent 75%),linear-gradient(180deg,#cfe0ea 0%,#9bb4c3 22%,#4e6a3c 45%,#5d7442 62%,#2e3e34 78%,#3a4a44 100%)}
.testi-title{left:120px;top:1722px;width:960px}
.quote{width:272px;height:194px;background:var(--white);text-align:center;padding:46px 28px 0;font-size:13px;line-height:21px}
.quote b{display:block;margin-top:10px;font-size:13px;color:var(--ink)}
.quote .qmark{position:absolute;right:22px;top:-18px;width:38px;height:38px;border-radius:50%;background:var(--caption);display:flex;align-items:center;justify-content:center}
.clients{left:0;top:2059px;width:1200px;height:186px;background:var(--band)}
.client{top:2138px;width:200px;text-align:center;font-family:"Jost",sans-serif;font-size:26px;font-weight:500;color:#b5b5b5}
.client-div{top:2100px;width:1px;height:100px;background:#d3d3d3}
.footer{left:0;top:2245px;width:1200px;height:233px;background:var(--footer)}
.foot-h{font-family:"Jost",sans-serif;font-size:23px;color:var(--ink)}
.links{left:113px;top:2340px;list-style:none;font-size:13px;line-height:21.5px;color:var(--text)}
.links li::before{content:"›";margin-right:12px;color:var(--ink)}
.field{background:var(--white);border:1px solid #d5d5d5;font-size:11px;color:var(--muted);padding:0 12px;display:flex;align-items:center;justify-content:space-between}
.subscribe{left:820px;top:2393px;width:129px;height:31px;line-height:31px;background:var(--btn);color:var(--ink);text-align:center;font-family:"Jost",sans-serif;font-size:17px;font-weight:500}
.bottom{left:0;top:2478px;width:1200px;height:54px;background:var(--bottom);color:#d0d0d0;font-size:12px;text-align:center;line-height:54px}
.dim{left:0;top:0;width:1200px;height:2532px;background:var(--dim)}
.modal{left:245px;top:169px;width:709px;height:484px;background:var(--white)}
.modal-title{left:413px;top:30px;font-family:"Jost",sans-serif;color:var(--black);line-height:1.12}
.modal-title .l1{font-size:34px;font-weight:400}
.modal-title .l2{font-size:35px;font-weight:600}
.input{left:410px;width:273px;height:39px;background:var(--field);font-size:13px;color:var(--ink);padding:10px 16px}
.submit{left:415px;top:393px;width:106px;height:32px;background:var(--black);color:var(--white);font-weight:700;font-size:15px;text-align:center;line-height:32px;border-radius:2px}
.partner{left:536px;top:396px;display:flex;align-items:center;gap:10px;font-family:"Jost",sans-serif;font-size:18px;color:#3a5a8a}
.partner i{width:26px;height:26px;border-radius:50%;background:#3a5a8a;display:block}
.close{left:948px;top:156px;width:26px;height:26px;border-radius:50%;background:var(--black);border:2px solid var(--white);color:var(--white);font-size:12px;font-weight:700;text-align:center;line-height:22px}
</style>
</head>
<body>
<header class="abs site-header">
  <div class="abs brand"><span class="mark"></span>QENO REALTY</div>
  <nav class="abs nav">
    <a class="active">Home</a><a>Qeno Info</a><a>About Qe No Home</a><a>Downloads</a><a>Contact us</a>
  </nav>
</header>

<section class="abs hero" role="img" aria-label="Slideshow photo of a lake house on a wooded Midwest lake"></section>
<svg class="abs hero-arrow" style="left:113px" width="22" height="34" viewBox="0 0 22 34"><path d="M18 3 4 17l14 14" fill="none" stroke="#fff" stroke-width="4"/></svg>
<svg class="abs hero-arrow" style="left:1065px" width="22" height="34" viewBox="0 0 22 34"><path d="M4 3l14 14L4 31" fill="none" stroke="#fff" stroke-width="4"/></svg>

<div class="abs intro-img" role="img" aria-label="Photo of a wood-panelled living room with lake view"></div>
<h2 class="abs sec-title intro-title">Qe No Info</h2>
<p class="abs intro-text">All the Lorem Ipsum generators on the Internet tend to repeat predefined chunks as necessary, making this the first true generator on the Internet.</p>
<a class="abs btn-more intro-more">Read more »</a>

<h2 class="abs sec-title popular-title">Popular Properties</h2>

<div class="abs card" style="left:113px;top:861px"><div class="photo" role="img" aria-label="Photo of a brick house beside a pond" style="background:radial-gradient(ellipse 40% 25% at 45% 48%,rgba(110,80,70,.8),transparent 75%),linear-gradient(180deg,#9bb6cf 0%,#b5c8d6 30%,#6c8a5a 52%,#5a7a8a 68%,#3e4f3a 100%)"></div><h3>Beautiful House</h3><p>Los Angels, 3654</p><svg width="22" height="22" viewBox="0 0 22 22"><g fill="none" stroke="#888" stroke-width="1.6"><rect x="2" y="9" width="10" height="6" rx="3" transform="rotate(-45 7 12)"/><rect x="10" y="7" width="10" height="6" rx="3" transform="rotate(-45 15 10)"/></g></svg></div>
<div class="abs card" style="left:361px;top:861px"><div class="photo" role="img" aria-label="Photo of a large stone manor with driveway" style="background:radial-gradient(ellipse 55% 30% at 50% 45%,rgba(120,100,90,.85),transparent 75%),linear-gradient(180deg,#aab7c2 0%,#8a8a88 35%,#6e6158 55%,#8a8580 72%,#5f7a48 100%)"></div><h3>Beautiful House</h3><p>Los Angels, 3654</p><svg width="22" height="22" viewBox="0 0 22 22"><g fill="none" stroke="#888" stroke-width="1.6"><rect x="2" y="9" width="10" height="6" rx="3" transform="rotate(-45 7 12)"/><rect x="10" y="7" width="10" height="6" rx="3" transform="rotate(-45 15 10)"/></g></svg></div>
<div class="abs card" style="left:606px;top:861px"><div class="photo" role="img" aria-label="Photo of a white colonial house with green lawn" style="background:radial-gradient(ellipse 40% 28% at 62% 45%,rgba(200,205,200,.85),transparent 75%),linear-gradient(180deg,#3f5e32 0%,#6a7e5a 35%,#9aa4a0 52%,#5f8a3e 75%,#4d7a34 100%)"></div><h3>Beautiful House</h3><p>Los Angels, 3654</p><svg width="22" height="22" viewBox="0 0 22 22"><g fill="none" stroke="#888" stroke-width="1.6"><rect x="2" y="9" width="10" height="6" rx="3" transform="rotate(-45 7 12)"/><rect x="10" y="7" width="10" height="6" rx="3" transform="rotate(-45 15 10)"/></g></svg></div>
<div class="abs card" style="left:851px;top:861px"><div class="photo" role="img" aria-label="Photo of a modern house at dusk" style="background:radial-gradient(ellipse 45% 20% at 55% 68%,rgba(220,150,90,.55),transparent 75%),linear-gradient(180deg,#5a6a9a 0%,#c0879a 30%,#5a4a4a 55%,#3a2e2a 100%)"></div><h3>Beautiful House</h3><p>Los Angels, 3654</p><svg width="22" height="22" viewBox="0 0 22 22"><g fill="none" stroke="#888" stroke-width="1.6"><rect x="2" y="9" width="10" height="6" rx="3" transform="rotate(-45 7 12)"/><rect x="10" y="7" width="10" height="6" rx="3" transform="rotate(-45 15 10)"/></g></svg></div>
<div class="abs card" style="left:113px;top:1148px"><div class="photo" role="img" aria-label="Photo of a white farmhouse lit at evening" style="background:radial-gradient(ellipse 45% 25% at 50% 40%,rgba(230,225,215,.7),transparent 75%),radial-gradient(ellipse 20% 12% at 25% 50%,rgba(240,190,110,.6),transparent 75%),linear-gradient(180deg,#4c5a78 0%,#7a7f8a 35%,#5a5a58 62%,#3a3a3a 100%)"></div><h3>Beautiful House</h3><p>Los Angels, 3654</p><svg width="22" height="22" viewBox="0 0 22 22"><g fill="none" stroke="#888" stroke-width="1.6"><rect x="2" y="9" width="10" height="6" rx="3" transform="rotate(-45 7 12)"/><rect x="10" y="7" width="10" height="6" rx="3" transform="rotate(-45 15 10)"/></g></svg></div>
<div class="abs card" style="left:361px;top:1148px"><div class="photo" role="img" aria-label="Photo of a brick family home among trees" style="background:radial-gradient(ellipse 50% 30% at 50% 55%,rgba(140,105,85,.85),transparent 75%),linear-gradient(180deg,#3e5a34 0%,#5b7a4a 30%,#7a6652 55%,#5e6a4a 75%,#4b6a3a 100%)"></div><h3>Beautiful House</h3><p>Los Angels, 3654</p><svg width="22" height="22" viewBox="0 0 22 22"><g fill="none" stroke="#888" stroke-width="1.6"><rect x="2" y="9" width="10" height="6" rx="3" transform="rotate(-45 7 12)"/><rect x="10" y="7" width="10" height="6" rx="3" transform="rotate(-45 15 10)"/></g></svg></div>
<div class="abs card" style="left:606px;top:1148px"><div class="photo" role="img" aria-label="Photo of a backyard pool at dusk" style="background:radial-gradient(ellipse 50% 28% at 40% 42%,rgba(235,190,110,.8),transparent 75%),linear-gradient(180deg,#3a4a7a 0%,#8a7a6a 30%,#c79a5a 48%,#3a9acc 70%,#2f7fa8 100%)"></div><h3>Beautiful House</h3><p>Los Angels, 3654</p><svg width="22" height="22" viewBox="0 0 22 22"><g fill="none" stroke="#888" stroke-width="1.6"><rect x="2" y="9" width="10" height="6" rx="3" transform="rotate(-45 7 12)"/><rect x="10" y="7" width="10" height="6" rx="3" transform="rotate(-45 15 10)"/></g></svg></div>
<div class="abs card" style="left:851px;top:1148px"><div class="photo" role="img" aria-label="Photo of stone cottages along a lane" style="background:radial-gradient(ellipse 40% 30% at 40% 50%,rgba(130,120,105,.85),transparent 75%),linear-gradient(180deg,#b8c4c8 0%,#8e8c80 30%,#7e7466 50%,#56703f 80%,#8a8a86 100%)"></div><h3>Beautiful House</h3><p>Los Angels, 3654</p><svg width="22" height="22" viewBox="0 0 22 22"><g fill="none" stroke="#888" stroke-width="1.6"><rect x="2" y="9" width="10" height="6" rx="3" transform="rotate(-45 7 12)"/><rect x="10" y="7" width="10" height="6" rx="3" transform="rotate(-45 15 10)"/></g></svg></div>

<h2 class="abs sec-title about-title">About Qe No Home</h2>
<p class="abs about-text">Luctus amet sollicitudin nec aliquam in. Et suspendisse interdum non enim sodales. Purus morbi sit et curabitur tellus in metus curabitur. Aenean posuere suspendisse. Curabitur neque varius augue est diam. At adipiscing in tem felis praesent. Eros morbi nam fringilla ...</p>
<a class="abs btn-more about-more">Read more »</a>
<div class="abs about-img" role="img" aria-label="Photo of a lakeside house among summer trees"></div>

<h2 class="abs sec-title testi-title">Testimonials</h2>
<div class="abs quote" style="left:113px;top:1815px">“Eros morbi nam fringilla sed quis est sem nonummy. Laoreet felis in morbi nulla condimentum vitae pede pede faucibus blandit inter-dum nec”<b>-Lara</b><span class="qmark"><svg width="16" height="12" viewBox="0 0 16 12"><path d="M1 12V7c0-4 2-6 5-7v2C4 3 4 5 4 6h3v6zm8 0V7c0-4 2-6 5-7v2c-2 1-2 3-2 4h3v6z" fill="#444"/></svg></span></div>
<div class="abs quote" style="left:466px;top:1815px">“Eros morbi nam fringilla sed quis est sem nonummy. Laoreet felis in morbi nulla condimentum vitae pede pede faucibus blandit inter-dum nec”<b>-Jhon</b><span class="qmark"><svg width="16" height="12" viewBox="0 0 16 12"><path d="M1 12V7c0-4 2-6 5-7v2C4 3 4 5 4 6h3v6zm8 0V7c0-4 2-6 5-7v2c-2 1-2 3-2 4h3v6z" fill="#444"/></svg></span></div>
<div class="abs quote" style="left:815px;top:1815px">“Eros morbi nam fringilla sed quis est sem nonummy. Laoreet felis in morbi nulla condimentum vitae pede pede faucibus blandit inter-dum nec”<b>-Ria</b><span class="qmark"><svg width="16" height="12" viewBox="0 0 16 12"><path d="M1 12V7c0-4 2-6 5-7v2C4 3 4 5 4 6h3v6zm8 0V7c0-4 2-6 5-7v2c-2 1-2 3-2 4h3v6z" fill="#444"/></svg></span></div>

<section class="abs clients"></section>
<svg class="abs" style="left:113px;top:2144px" width="16" height="28" viewBox="0 0 16 28"><path d="M13 2 3 14l10 12" fill="none" stroke="#bbb" stroke-width="3"/></svg>
<svg class="abs" style="left:1069px;top:2144px" width="16" height="28" viewBox="0 0 16 28"><path d="M3 2l10 12L3 26" fill="none" stroke="#bbb" stroke-width="3"/></svg>
<div class="abs client-div" style="left:158px"></div>
<div class="abs client" style="left:140px">Fizzwell</div>
<div class="abs client-div" style="left:340px"></div>
<div class="abs client" style="left:387px">Orvexa</div>
<div class="abs client-div" style="left:635px"></div>
<div class="abs client" style="left:633px">Nimbly</div>
<div class="abs client-div" style="left:880px"></div>
<div class="abs client" style="left:860px;font-size:20px;top:2142px">Brickhaus Labs</div>
<div class="abs client-div" style="left:1040px"></div>

<footer class="abs footer"></footer>
<h3 class="abs foot-h" style="left:113px;top:2292px">Links</h3>
<ul class="abs links"><li>Home</li><li>Qeno Info</li><li>About Qe No Home</li><li>Downloads</li><li>Contact us</li></ul>
<h3 class="abs foot-h" style="left:398px;top:2290px">Search</h3>
<div class="abs field" style="left:398px;top:2341px;width:328px;height:36px">Search Now<svg width="16" height="16" viewBox="0 0 16 16"><circle cx="6.5" cy="6.5" r="5" fill="none" stroke="#777" stroke-width="2"/><path d="M10 10l5 5" stroke="#777" stroke-width="2"/></svg></div>
<h3 class="abs foot-h" style="left:820px;top:2292px">Newsletter Subscribe</h3>
<div class="abs field" style="left:820px;top:2340px;width:265px;height:37px">Email id<svg width="16" height="12" viewBox="0 0 16 12"><rect x="1" y="1" width="14" height="10" fill="none" stroke="#777" stroke-width="1.5"/><path d="M1 1l7 6 7-6" fill="none" stroke="#777" stroke-width="1.5"/></svg></div>
<div class="abs subscribe">Subscribe</div>

<div class="abs bottom">© copyrights 2018 &nbsp;|&nbsp; www.qenorealty.com</div>
<svg class="abs" style="left:1091px;top:2498px" width="14" height="10" viewBox="0 0 14 10"><path d="M1 8l6-6 6 6" fill="none" stroke="#ddd" stroke-width="2"/></svg>

<div class="abs dim"></div>

<div class="abs modal">
  <svg class="abs" style="left:0;top:0" width="440" height="484" viewBox="0 0 440 484">
    <defs>
      <linearGradient id="house" x1="0" y1="0" x2="0" y2="1"><stop offset="0" stop-color="#7d8f6e"/><stop offset=".22" stop-color="#8a5a4a"/><stop offset=".4" stop-color="#a49c90"/><stop offset=".62" stop-color="#d4d1c8"/><stop offset=".74" stop-color="#e8e8e4"/><stop offset=".8" stop-color="#6a9a3a"/><stop offset="1" stop-color="#4a7a2a"/></linearGradient>
    </defs>
    <path d="M0 70C80 30 180 20 240 60c60 40 50 110 110 155 70 50 80 185 20 269H0z" fill="#ececec"/>
    <path role="img" aria-label="Photo of a stucco luxury home with tiled roof and lawn" d="M0 100C60 60 150 50 200 80c60 35 50 110 120 150 70 40 80 170 20 254H0z" fill="url(#house)"/>
  </svg>
  <div class="abs modal-title"><div class="l1">My Free</div><div class="l2">Market Analysis</div></div>
  <div class="abs input" style="top:123px">Full Name</div>
  <div class="abs input" style="top:172px">Email Address</div>
  <div class="abs input" style="top:221px">Phone Number</div>
  <div class="abs input" style="top:270px;height:106px">Address</div>
  <div class="abs submit">SUBMIT</div>
  <div class="abs partner"><i></i>PostPlume</div>
</div>
<div class="abs close">X</div>
</body>
</html>
```